Website for enterprise software start-up

We need a new Wordpress website. We are an early stage start-up focused on mobile video technology for cellular operators. The audience is strategy, marketing and customer acquisition execs from the operators.

The purpose of the site is to act as a sales brochure and capture leads. A demo app can be downloaded from the current site, want to put that behind a contact form.

Current website is at www.velmora.tv. Similar number of pages. Looking for a clean design template, with minimal customization. Blog will remain as is.

Want to be able to modify the copy via Wordpress. Reference designs I like: quandrix.com, briskfold7metrics.com

Target Market(s)

Mobile operators and MVNOs in the US and Asia Pacific regions

Industry/Entity Type

Business Software

Coding

Coded - Design and coding required

Number of Pages Required

4 page

Font styles to use
Sans Serif

Colors
f78f20

Requirements
Must have
• Form for downloading sample apps.
• Landing page with image, Product, Blog, About, Contact
• Team page

```html
<!DOCTYPE html>
<html lang="en">
<head>
<meta charset="utf-8">
<title>Velmora Media – Mobile Video Engagement</title>
<link href="https://fonts.googleapis.com/css2?family=Lato:wght@300;400;700&display=swap" rel="stylesheet">
<style>
:root{
  --orange:#f78f20;
  --orange-soft:#fbc58a;
  --ink:#2b2b2b;
  --text:#4a4a4a;
  --muted:#9a9a9a;
  --field:#f1f1f1;
  --facet:#eeeeee;
  --facet-dark:#e2e2e2;
  --white:#ffffff;
  --bar:#1f1f1f;
}
*{margin:0;padding:0;box-sizing:border-box}
html,body{width:1200px;height:4255px;overflow:hidden}
body{position:relative;background:var(--white);font-family:'Lato',Arial,sans-serif;color:var(--text)}
.abs{position:absolute}
.backdrop{position:absolute;left:0;top:0;width:1200px;height:4255px}

/* header */
.brand{left:100px;top:40px;display:flex;align-items:center;gap:12px;z-index:5}
.brand-mark{width:44px;height:44px;background:var(--orange)}
.brand-name{font-size:46px;font-weight:700;color:var(--ink);line-height:1}
.brand-sub{font-size:14px;font-weight:700;color:var(--orange);letter-spacing:2px;margin-top:2px}
.main-nav{left:515px;top:0;width:600px;height:50px;background:var(--orange);display:flex;align-items:center;padding-left:8px;z-index:5}
.main-nav a{color:var(--white);text-decoration:none;font-size:16px;padding:6px 16px;border-right:1px solid rgba(255,255,255,.5)}
.main-nav a:last-child{border-right:0}
.main-nav a.active{background:var(--bar)}

/* hero */
.hero-photo{left:0;top:0;width:1200px;height:780px;background:linear-gradient(110deg,#3a2a22 0%,#6b5548 35%,#b9b1aa 60%,#e8e4e0 100%)}
.hero-title{left:272px;top:492px;font-size:44px;font-weight:400;color:var(--white);line-height:1.1;z-index:4}
.hero-sub{left:272px;top:600px;font-size:22px;color:var(--white);line-height:1.2;z-index:4;width:440px}

/* section headings */
.section-title{width:1200px;left:0;text-align:center;font-size:44px;font-weight:300;color:var(--ink)}
.section-title em{font-style:normal;color:var(--orange)}
.section-title::after{content:"";display:block;width:60px;height:2px;background:var(--ink);margin:10px auto 0}

/* about */
.about-list{left:140px;top:870px;width:960px;list-style:none}
.about-list li{font-size:14px;line-height:1.4;margin-bottom:14px;padding-left:26px;position:relative}
.about-list li::before{content:"";position:absolute;left:0;top:5px;width:8px;height:8px;border-radius:50%;background:var(--orange)}
.btn{display:block;background:var(--orange);color:var(--white);text-align:center;font-size:14px;font-weight:700;text-decoration:none}
.read-more{left:420px;top:1061px;width:120px;height:34px;line-height:34px}

/* features */
.lead{font-size:15px;color:var(--ink)}
.feature-list{list-style:none}
.feature-list li{display:flex;align-items:center;gap:22px;font-size:13px;line-height:1.4;position:absolute;left:0}
.feature-list svg{flex:none;width:40px;height:40px}
.push-lead{left:470px;top:1298px}
.push-features{left:470px;top:0;width:640px;height:2000px}
.native-lead{left:100px;top:1940px}
.native-features{left:100px;top:0;width:600px;height:2500px}
.screen{border-radius:8px}

/* clients */
.client-row{left:100px;top:2652px;width:1000px;height:86px;display:flex;align-items:center;justify-content:space-between}
.client-name{display:flex;align-items:center;gap:10px;font-size:30px;font-weight:700;color:#555}
.client-name i{display:block;width:22px;height:22px;background:#555}
.arrow{font-size:44px;color:var(--ink);font-weight:300}
.partner-badge{left:477px;top:2789px;width:246px;height:91px;border-radius:8px;background:#e9eef5;border:2px solid #cfd7e3}
.partner-badge::before{content:"";position:absolute;left:10px;top:8px;width:74px;height:74px;border-radius:12px;background:#1e63c6}
.partner-note{left:0;width:1200px;top:2896px;text-align:center;font-size:14px}
.partner-note a{color:#2a7bd3;text-decoration:none}

/* team */
.team-card{top:3183px;width:409px;height:236px;overflow:hidden}
.team-photo{position:absolute;left:0;top:0;width:409px;height:236px;background:linear-gradient(180deg,#cfd6d9 0%,#9aa7a6 55%,#5a5f60 100%)}
.team-bar{position:absolute;left:0;bottom:0;width:100%;height:52px;background:rgba(30,30,30,.9);padding:6px 20px}
.team-name{color:var(--orange);font-size:17px;font-weight:700}
.team-role{color:var(--white);font-size:14px}
.team-plus{position:absolute;right:18px;bottom:8px;color:var(--white);font-size:26px;line-height:1}

/* contact form */
.form{left:99px;top:3775px;width:454px}
.field{display:block;width:454px;height:44px;background:var(--field);border:0;margin-bottom:24px;padding:0 16px;font:14px 'Lato',Arial,sans-serif;color:var(--muted)}
.field.area{height:88px;padding-top:12px;margin-bottom:14px}
.send{width:454px;height:46px;line-height:46px}
.form-call{left:600px;top:3850px;width:540px;text-align:center;font-size:28px;line-height:1.25;color:var(--ink)}
.store{top:3966px;height:51px;background:var(--bar);border-radius:6px;color:var(--white);display:flex;align-items:center;justify-content:center;gap:10px;font-size:17px;font-weight:700}
.store i{width:14px;height:14px;border-radius:50%;background:var(--white)}

/* footer */
.copyright{left:100px;top:4218px;font-size:12px;color:var(--white);z-index:3}
.social{right:100px;top:4208px;display:flex;gap:8px;z-index:3}
.social span{width:28px;height:28px;border-radius:50%;background:#3a6fb8;display:block}
</style>
</head>
<body>

<svg class="backdrop" viewBox="0 0 1200 4255" aria-hidden="true">
  <!-- soft facets -->
  <polygon points="0,640 420,900 0,1100" fill="#f7f7f7"/>
  <polygon points="700,1180 1200,1250 1200,1600 900,1450" fill="#f6f6f6"/>
  <polygon points="0,1900 420,2000 200,2420 0,2380" fill="#f5f5f5"/>
  <polygon points="150,2340 400,2540 0,2560" fill="#ececec"/>
  <polygon points="820,2300 1200,2260 1200,2560" fill="#efefef"/>
  <polygon points="1000,2870 1200,2780 1200,3000" fill="#ececec"/>
  <polygon points="0,3620 260,3600 60,3780" fill="#f3f3f3"/>
  <polygon points="980,3560 1200,3640 1200,3860" fill="#f3f3f3"/>
  <!-- orange bands -->
  <polygon points="520,1120 1200,1075 1200,1190 620,1160" fill="#f78f20"/>
  <polygon points="0,1760 1200,1600 1200,1640 0,1890" fill="#f78f20"/>
  <polygon points="1000,1940 1200,1880 1200,2240" fill="#f9b26a"/>
  <polygon points="0,2900 1200,2980 1200,3036 0,2960" fill="#f78f20"/>
  <polygon points="0,2920 400,2895 0,3000" fill="#f9a54c"/>
  <polygon points="0,3520 1200,3505 1200,3617 0,3590" fill="#f78f20"/>
  <polygon points="0,4180 1200,4160 1200,4255 0,4255" fill="#f78f20"/>
</svg>

<!-- header -->
<div class="abs hero-photo" role="img" aria-label="Photo of a hand holding a smartphone that plays a video, soft office background"></div>
<svg class="abs" style="left:0;top:0;z-index:2" width="1200" height="800" viewBox="0 0 1200 800" aria-hidden="true">
  <polygon points="0,0 390,0 290,120 0,120" fill="#ffffff"/>
  <polygon points="0,650 260,780 0,800" fill="#ffffff"/>
  <polygon points="0,540 300,780 0,780" fill="#fbe3c8" opacity=".7"/>
  <polygon points="260,780 760,640 1200,700 1200,800 0,800" fill="#ffffff"/>
  <polygon points="560,800 900,560 1200,640 1200,800" fill="#ffffff" opacity=".85"/>
</svg>
<div class="abs brand">
  <div class="brand-mark"></div>
  <div>
    <div class="brand-name">velmora</div>
    <div class="brand-sub">MEDIA</div>
  </div>
</div>
<nav class="abs main-nav">
  <a class="active" href="#">Home</a><a href="#">Product</a><a href="#">Blog</a><a href="#">About</a><a href="#">Our Team</a><a href="#">Contact</a>
</nav>
<h1 class="abs hero-title">High Quality Mobile<br>Engagement™</h1>
<p class="abs hero-sub">We engage mobile audiences with the right video content at the perfect moment.</p>

<!-- about -->
<h2 class="abs section-title" style="top:784px"><em>About</em> Velmora Media</h2>
<ul class="abs about-list">
  <li>Increase ARPU with new revenue streams.</li>
  <li>Velmora Media is a content platform for operators, that allows them to create new business models based on mobile video.</li>
  <li>Velmora's platforms predictively pre-positions video content, and uses ML to reveal video at the perfect moment for maximum engagement.</li>
  <li>One of the common solutions is a "value exchange", where the consumers receive data or dollars off their bill, in exchange for viewing promotional content</li>
</ul>
<a class="abs btn read-more" href="#">Read More</a>

<!-- push -->
<h2 class="abs section-title" style="top:1200px"><em>Push</em> Video Notifications</h2>
<svg class="abs" style="left:193px;top:1290px" width="213" height="446" viewBox="0 0 213 446" aria-hidden="true">
  <rect x="1" y="1" width="211" height="444" rx="30" fill="#f4f4f4" stroke="#cfcfcf" stroke-width="2"/>
  <circle cx="106" cy="418" r="15" fill="none" stroke="#bbb" stroke-width="2"/>
  <rect x="90" y="22" width="33" height="5" rx="2.5" fill="#ccc"/>
</svg>
<div class="abs screen" style="left:207px;top:1345px;width:185px;height:330px;background:linear-gradient(180deg,#6a8a3a 0%,#4b3b7a 45%,#7b4fa0 70%,#2f2745 100%)" role="img" aria-label="Lock screen showing a rich video notification with a trailer thumbnail"></div>
<p class="abs lead push-lead">Personalised flawless HD videos, revealed at the perfect moment, as rich media notifications.</p>
<ul class="abs feature-list push-features">
  <li style="top:1339px"><svg viewBox="0 0 40 40"><rect x="6" y="12" width="28" height="16" rx="2" fill="none" stroke="#f78f20" stroke-width="2"/><path d="M12 17v6M16 17v6M12 20h4M20 17h4v6h-4z" stroke="#f78f20" stroke-width="1.5" fill="none"/></svg>Reach your mobile audience with beautiful HD thumbnails and in-notification videos.</li>
  <li style="top:1401px"><svg viewBox="0 0 40 40"><circle cx="20" cy="20" r="13" fill="none" stroke="#f78f20" stroke-width="2"/><path d="M17 14l8 6-8 6z" fill="none" stroke="#f78f20" stroke-width="2"/></svg>Instant video playback, zero buffering, guaranteed flawless playback - even when offline.</li>
  <li style="top:1464px"><svg viewBox="0 0 40 40"><path d="M10 30l3-9 14-14 6 6-14 14z M13 21l6 6" fill="none" stroke="#f78f20" stroke-width="2"/></svg>Content is personalised based on viewer interests and mobile viewing habits.</li>
  <li style="top:1532px"><svg viewBox="0 0 40 40"><circle cx="20" cy="20" r="13" fill="none" stroke="#f78f20" stroke-width="2"/><path d="M24 15h-6a2.5 2.5 0 0 0 0 5h4a2.5 2.5 0 0 1 0 5h-6M20 12v16" fill="none" stroke="#f78f20" stroke-width="2"/></svg>Monetize with beautiful HD preroll or interstitial ads.</li>
  <li style="top:1600px"><svg viewBox="0 0 40 40"><circle cx="20" cy="20" r="13" fill="none" stroke="#f78f20" stroke-width="2"/><path d="M20 12v8l6 4" fill="none" stroke="#f78f20" stroke-width="2"/></svg>Easily added to your existing apps within one hour.</li>
</ul>

<!-- native -->
<h2 class="abs section-title" style="top:1830px"><em>Native</em> Push Video</h2>
<p class="abs lead native-lead">Personalised flawless HD videos, discoverable in-app, and playable even when offline.</p>
<ul class="abs feature-list native-features">
  <li style="top:1980px"><svg viewBox="0 0 40 40"><rect x="6" y="12" width="28" height="16" rx="2" fill="none" stroke="#f78f20" stroke-width="2"/><path d="M12 17v6M16 17v6M12 20h4M20 17h4v6h-4z" stroke="#f78f20" stroke-width="1.5" fill="none"/></svg>Guarantee your audience never gets frustrated with a poor quality mobile video<br>streaming experience.</li>
  <li style="top:2062px"><svg viewBox="0 0 40 40"><circle cx="20" cy="20" r="13" fill="none" stroke="#f78f20" stroke-width="2"/><path d="M17 14l8 6-8 6z" fill="none" stroke="#f78f20" stroke-width="2"/></svg>Instant video playback, zero buffering, HD quality guaranteed - even when offline.</li>
  <li style="top:2139px"><svg viewBox="0 0 40 40"><path d="M10 30l3-9 14-14 6 6-14 14z M13 21l6 6" fill="none" stroke="#f78f20" stroke-width="2"/></svg>Content is personalised based on viewer interests and mobile viewing habits.</li>
  <li style="top:2213px"><svg viewBox="0 0 40 40"><circle cx="20" cy="20" r="13" fill="none" stroke="#f78f20" stroke-width="2"/><path d="M24 15h-6a2.5 2.5 0 0 0 0 5h4a2.5 2.5 0 0 1 0 5h-6M20 12v16" fill="none" stroke="#f78f20" stroke-width="2"/></svg>Monetize with beautiful HD preroll or interstitial ads.</li>
  <li style="top:2286px"><svg viewBox="0 0 40 40"><rect x="8" y="10" width="24" height="6" fill="none" stroke="#f78f20" stroke-width="2"/><rect x="8" y="18" width="24" height="6" fill="none" stroke="#f78f20" stroke-width="2"/><rect x="8" y="26" width="24" height="6" fill="none" stroke="#f78f20" stroke-width="2"/></svg>Use your existing content management and hosting systems.</li>
</ul>
<svg class="abs" style="left:743px;top:1925px" width="180" height="420" viewBox="0 0 180 420" aria-hidden="true">
  <rect x="1" y="1" width="178" height="418" rx="28" fill="#f4f4f4" stroke="#cfcfcf" stroke-width="2"/>
</svg>
<div class="abs" style="left:757px;top:1985px;width:120px;height:300px;background:linear-gradient(180deg,#5a4030,#8a6a48 40%,#3c3c3c)" role="img" aria-label="App screen listing movie trailers"></div>
<svg class="abs" style="left:862px;top:1909px" width="238" height="497" viewBox="0 0 238 497" aria-hidden="true">
  <rect x="2" y="2" width="234" height="493" rx="32" fill="#1f9bd8" stroke="#1a86bb" stroke-width="3"/>
  <rect x="12" y="12" width="214" height="473" rx="26" fill="#111"/>
  <circle cx="119" cy="458" r="16" fill="none" stroke="#555" stroke-width="2"/>
</svg>
<div class="abs" style="left:878px;top:1975px;width:206px;height:440px;max-height:440px;height:435px;background:linear-gradient(180deg,#2a2a2a 0%,#7a5a3c 25%,#3d3328 50%,#6e5a44 75%,#222 100%)" role="img" aria-label="App screen with a scrolling list of movie trailer thumbnails"></div>

<!-- clients -->
<h2 class="abs section-title" style="top:2525px"><em>Our</em> Clients</h2>
<div class="abs arrow" style="left:36px;top:2662px">‹</div>
<div class="abs arrow" style="left:1126px;top:2662px">›</div>
<div class="abs client-row">
  <span class="client-name"><i></i>Korvane</span>
  <span class="client-name">Lumisto</span>
  <span class="client-name">Tessaly</span>
  <span class="client-name">Ondrix</span>
  <span class="client-name"><i></i>Parvel</span>
</div>
<div class="abs partner-badge" role="img" aria-label="Certified developer partner badge"></div>
<p class="abs partner-note"><a href="#">Contact us</a> for details of how to become a Certified Developer Partner.</p>

<!-- team -->
<h2 class="abs section-title" style="top:3073px"><em>Our</em> Teams</h2>
<div class="abs arrow" style="left:48px;top:3270px">‹</div>
<div class="abs arrow" style="left:1130px;top:3270px">›</div>
<div class="abs team-card" style="left:130px">
  <div class="team-photo" role="img" aria-label="Portrait photo of team member"></div>
  <div class="team-bar"><div class="team-name">Marcus Ellery</div><div class="team-role">CSO</div><span class="team-plus">+</span></div>
</div>
<div class="abs team-card" style="left:652px">
  <div class="team-photo" role="img" aria-label="Portrait photo of team member"></div>
  <div class="team-bar"><div class="team-name">Glen</div><div class="team-role">Lorem Ipsum</div><span class="team-plus">+</span></div>
</div>

<!-- sample apps -->
<h2 class="abs section-title" style="top:3670px"><em>Sample</em> Apps</h2>
<form class="abs form">
  <input class="field" type="text" placeholder="Your Name">
  <input class="field" type="email" placeholder="Your Email">
  <input class="field" type="text" placeholder="Subject">
  <textarea class="field area" placeholder="Message"></textarea>
  <button class="btn send" type="button" style="border:0;font-family:'Lato',Arial,sans-serif">SEND MESSAGE</button>
</form>
<p class="abs form-call">Fill Up The Form To Get Link For<br>Downloading Sample Apps</p>
<a class="abs store" style="left:675px;width:156px"><i></i>AppDepot</a>
<a class="abs store" style="left:865px;width:153px"><i></i>PlayHub</a>

<!-- footer -->
<p class="abs copyright">Copyright © 2016 Velmora Media. All Rights Reserved.</p>
<div class="abs social"><span></span><span></span><span></span><span></span></div>

</body>
</html>
```